Verdant Systems Business Card

want the back of card to be blue- with the logo in the center
front of card- info plus logo (info being mailing address, email address, and website address )
4 different names with titles to have on cards
1) Calvin Borsted - Owner
2) Naomi Trelvik- Customer Relationship Specialist
3) Felix Andrade- Vice President of Sales
4) Owen Markby- Chief Technology Officer

Target Market(s)

tech company in the government/probation office industry

Industry/Entity Type

Government Office

Contact Information for Business Card

1) Calvin Borsted - Owner

Colors
0355a3
ffffff

Requirements
Must have
• back side should be blue, with the logo placed in the center
• front side needs to include both the logo, as well as company info (info should include website address, email address, and mailing address)

```html
<!DOCTYPE html>
<html lang="en">
<head>
<meta charset="utf-8">
<title>Verdant Systems Business Cards</title>
<link href="https://fonts.googleapis.com/css2?family=Libre+Baskerville:wght@700&family=Roboto:wght@300;400&display=swap" rel="stylesheet">
<style>
  :root {
    --navy: #172b52;
    --white: #ffffff;
    --gray: #7d7f84;
    --backdrop: #7a4526;
  }
  * { margin: 0; padding: 0; box-sizing: border-box; }
  html, body { width: 1200px; height: 1117px; overflow: hidden; }
  body { background: var(--backdrop); position: relative; font-family: "Roboto", sans-serif; }

  .card {
    position: absolute;
    width: 470px;
    height: 269px;
    background: var(--white);
    overflow: hidden;
    box-shadow: 0 2px 6px rgba(0,0,0,0.35);
  }
  .card--naomi  { left: 101px; top: 104px; }
  .card--felix  { left: 629px; top: 104px; }
  .card--owen   { left: 101px; top: 433px; }
  .card--calvin { left: 629px; top: 433px; }

  .card__band {
    position: absolute;
    left: 0; right: 0; bottom: 0;
    background: var(--navy);
  }
  .card--naomi  .card__band { top: 156px; }
  .card--felix  .card__band { top: 162px; }
  .card--owen   .card__band { top: 168px; }
  .card--calvin .card__band { top: 165px; }

  .person { position: absolute; left: 29px; top: 34px; }
  .person__name {
    font-family: "Libre Baskerville", serif;
    font-weight: 700;
    font-size: 19px;
    color: var(--navy);
    line-height: 1.1;
  }
  .person__title {
    font-size: 12.5px;
    color: var(--gray);
    margin-top: 1px;
  }

  .wordmark {
    position: absolute;
    right: 36px; top: 36px;
    font-family: "Libre Baskerville", serif;
    font-weight: 700;
    font-size: 21px;
    color: var(--navy);
  }

  .contact {
    position: absolute;
    left: 29px;
    color: var(--white);
    font-size: 12px;
    line-height: 15px;
    list-style: none;
  }
  .contact li { display: flex; align-items: center; }
  .contact svg { width: 10px; height: 10px; margin-right: 7px; flex: none; }
  .contact .contact__address { display: block; }
  .contact .contact__gap { margin-top: 3px; }
  .card--naomi  .contact { top: 166px; }
  .card--felix  .contact { top: 175px; }
  .card--owen   .contact { top: 179px; }
  .card--calvin .contact { top: 180px; }

  .card--back {
    left: 365px; top: 770px;
    background: var(--navy);
    display: flex; align-items: center; justify-content: center;
  }
  .card--back .wordmark {
    position: static;
    color: var(--white);
    font-size: 26px;
  }
</style>
</head>
<body>
<svg width="0" height="0" style="position:absolute">
  <defs>
    <symbol id="icon-phone" viewBox="0 0 10 10"><path fill="#fff" d="M2 0.5l1.6 2-1 1c.6 1.3 1.6 2.3 2.9 2.9l1-1 2 1.6-1 1.8C4.4 8.6 1.4 5.6.3 1.5z"/></symbol>
    <symbol id="icon-mobile" viewBox="0 0 10 10"><rect x="2.3" y="0.5" width="5.4" height="9" rx="0.8" fill="none" stroke="#fff" stroke-width="1.2"/></symbol>
    <symbol id="icon-mail" viewBox="0 0 10 10"><rect x="0.5" y="2.2" width="9" height="6" fill="#fff"/><path d="M0.8 2.6L5 5.8l4.2-3.2" fill="none" stroke="#172b52" stroke-width="0.8"/></symbol>
    <symbol id="icon-web" viewBox="0 0 10 10"><circle cx="5" cy="5" r="4.5" fill="#fff"/><path d="M3 2.5c1 .5 1 1.5 0 2s0 2 1 2.5M6.5 3c-.5 1 .5 1.5 1.5 1.5" fill="none" stroke="#172b52" stroke-width="0.9"/></symbol>
  </defs>
</svg>

<section class="card card--naomi">
  <div class="card__band"></div>
  <div class="person"><p class="person__name">Naomi Trelvik</p><p class="person__title">Customer Relationship Manager</p></div>
  <p class="wordmark">Verdant Systems</p>
  <ul class="contact">
    <li class="contact__address">418 Fenwick Drive</li>
    <li class="contact__address">Suite C, Carrow, GA 30977</li>
    <li class="contact__gap"><svg><use href="#icon-phone"/></svg>555-201-4410 ext 1000</li>
    <li><svg><use href="#icon-mobile"/></svg>555-308-2217</li>
    <li><svg><use href="#icon-mail"/></svg>ntrelvik@verdantsystems.com</li>
    <li><svg><use href="#icon-web"/></svg>www.verdantsystems.com</li>
  </ul>
</section>

<section class="card card--felix">
  <div class="card__band"></div>
  <div class="person"><p class="person__name">Felix Andrade</p><p class="person__title">Vice President of Sales</p></div>
  <p class="wordmark">Verdant Systems</p>
  <ul class="contact">
    <li class="contact__address">418 Fenwick Drive, Suite C</li>
    <li class="contact__address">Carrow, GA 30977</li>
    <li class="contact__gap"><svg><use href="#icon-mobile"/></svg>555-412-6093</li>
    <li><svg><use href="#icon-mail"/></svg>fandrade@verdantsystems.com</li>
    <li><svg><use href="#icon-web"/></svg>www.verdantsystems.com</li>
  </ul>
</section>

<section class="card card--owen">
  <div class="card__band"></div>
  <div class="person"><p class="person__name">Owen Markby</p><p class="person__title">Chief Technology Officer</p></div>
  <p class="wordmark">Verdant Systems</p>
  <ul class="contact">
    <li class="contact__address">418 Fenwick Drive</li>
    <li class="contact__address">Suite C, Carrow, GA 30977</li>
    <li class="contact__gap"><svg><use href="#icon-mobile"/></svg>555-417-3382</li>
    <li><svg><use href="#icon-mail"/></svg>omarkby@verdantsystems.com</li>
    <li><svg><use href="#icon-web"/></svg>www.verdantsystems.com</li>
  </ul>
</section>

<section class="card card--calvin">
  <div class="card__band"></div>
  <div class="person"><p class="person__name">Calvin Borsted</p><p class="person__title">Owner</p></div>
  <p class="wordmark">Verdant Systems</p>
  <ul class="contact">
    <li><svg><use href="#icon-phone"/></svg>555-201-4400</li>
    <li><svg><use href="#icon-mobile"/></svg>555-419-7751</li>
    <li><svg><use href="#icon-mail"/></svg>cborsted@verdantsystems.com</li>
    <li><svg><use href="#icon-web"/></svg>www.verdantsystems.com</li>
    <li class="contact__address contact__gap">418 Fenwick Drive, Suite C, Carrow, GA 30977</li>
  </ul>
</section>

<section class="card card--back">
  <p class="wordmark">Verdant Systems</p>
</section>
</body>
</html>
```